Allied Health team of Physiotherapists & Occupational Therapists seek a business card design

We have our new logo, we now need our new business cards and stationary. Tidewell: Oedema & Family Clinic is seeking a generic card design to represent our whole team and individual cards for each therapist that incorporates our new logo to communicate our holistic approach that is calming, nuturing, supportive and welcoming.
Our Physiotherapists and Occupational Therapists assess, treat and provide education for people who are at risk of or who have lymphoedema. This is often as a result of treatment for cancer. We provide pre-operative and post-operative management and cancer rehabilitation in our Pilates studio. Our team also consists of Physiotherapists who have a strong interest in pelvic floor and continence management for both men and women.

Target Market(s)

Mainly women health conscious

Industry/Entity Type

Allied Health: Physiotherapy / Occupational Therapy

Contact Information for Business Card

Address: 14 Gallivant Ave Marlow Bay 3921 Phone: 84316570 fax: 8431 6578 Email: info@tidewellcareservices.com.au Website: tidewellcareservices.com.au Facebook address: friendhub.net/TidewellOedemaAndFamilyCareClinic. Room to write appointments. Individual cards need to have name, office email and individual email and professional details

Requirements
Must have
• Logo as per uploaded documents

```html
<!DOCTYPE html>
<html lang="en">
<head>
<meta charset="utf-8">
<title>Tidewell: Oedema &amp; Family Clinic — Business Cards</title>
<link rel="stylesheet" href="https://fonts.googleapis.com/css2?family=Andika:wght@400&family=Open+Sans:ital,wght@0,400;1,400&display=swap">
<style>
  :root {
    --stage: #2b2b2b;
    --card-white: #ffffff;
    --card-dark: #1d1d1d;
    --peach: #f5a878;
    --peach-faint: #fbefe8;
    --ink: #333333;
    --rule: #dddddd;
    --on-dark: #ffffff;
  }
  * { margin: 0; padding: 0; box-sizing: border-box; }
  html, body {
    width: 1200px; height: 1015px; overflow: hidden;
    background: var(--stage);
  }
  .sheet {
    width: 1200px; height: 1015px;
    display: flex; flex-direction: column; align-items: center; justify-content: center;
    gap: 40px;
  }
  .card {
    position: relative;
    width: 780px; height: 446px;
    overflow: hidden;
    box-shadow: 0 10px 30px rgba(0,0,0,.45);
  }

  /* Appointment side */
  .card--appointment { background: var(--card-white); }
  .watermark {
    position: absolute; left: 360px; top: 48px;
    width: 300px; height: 300px;
    display: flex; align-items: center; justify-content: center;
  }
  .watermark .ring {
    position: absolute; inset: 0;
    border-radius: 50%;
    border: 2px solid var(--peach-faint);
  }
  .watermark .name {
    font-family: "Andika", sans-serif;
    font-size: 64px; color: var(--peach-faint);
  }
  .appointment-title {
    position: absolute; left: 0; right: 0; top: 70px;
    text-align: center;
    font-family: "Andika", sans-serif;
    font-weight: 400;
    font-size: 42px; letter-spacing: 2px;
    color: var(--peach);
  }
  .write-lines {
    position: absolute; left: 230px; width: 360px; top: 175px;
    display: flex; flex-direction: column; gap: 62px;
  }
  .write-lines span { display: block; height: 1px; background: var(--rule); }
  .cancellation-note {
    position: absolute; left: 0; right: 0; bottom: 40px;
    text-align: center;
    font-family: "Open Sans", sans-serif;
    font-size: 15px; line-height: 1.3;
    color: var(--ink);
  }

  /* Contact side */
  .card--contact { background: var(--card-dark); }
  .card--contact .backdrop { position: absolute; inset: 0; width: 780px; height: 446px; }
  .brand {
    position: absolute; left: 540px; top: 100px;
    width: 200px; height: 130px;
    display: flex; flex-direction: column; align-items: center; justify-content: center; gap: 10px;
  }
  .brand .mark {
    width: 24px; height: 24px; border-radius: 50%;
    background: var(--peach);
  }
  .brand .name {
    font-family: "Andika", sans-serif;
    font-size: 46px; color: var(--peach);
  }
  .contact-list {
    position: absolute; left: 48px; top: 96px;
    list-style: none;
    font-family: "Open Sans", sans-serif;
    font-size: 18px; color: var(--on-dark);
    display: flex; flex-direction: column; gap: 6px;
  }
  .contact-list li { display: flex; align-items: center; gap: 12px; }
  .contact-list li.address { margin-top: 18px; }
  .contact-list svg { width: 18px; height: 18px; flex: none; fill: var(--peach); }
  .book-online {
    position: absolute; left: 90px; top: 300px;
    font-family: "Andika", sans-serif;
    font-size: 62px; letter-spacing: 3px; line-height: 1;
    color: var(--peach);
  }
  .social {
    position: absolute; left: 90px; bottom: 28px;
    font-family: "Open Sans", sans-serif; font-style: italic;
    font-size: 16px; color: var(--on-dark);
  }
</style>
</head>
<body>
<main class="sheet">

  <section class="card card--appointment" aria-label="Appointment card">
    <div class="watermark" aria-hidden="true">
      <span class="ring"></span>
      <span class="name">Tidewell</span>
    </div>
    <h2 class="appointment-title">Next Appointment</h2>
    <div class="write-lines" aria-hidden="true"><span></span><span></span><span></span></div>
    <p class="cancellation-note">Please give me 24 hours notice if you are unable to keep your<br>appointment or a cancellation fee may be charged</p>
  </section>

  <section class="card card--contact" aria-label="Contact card">
    <svg class="backdrop" viewBox="0 0 780 446" aria-hidden="true">
      <circle cx="626" cy="164" r="238" fill="none" stroke="#f5a878" stroke-width="4"/>
      <circle cx="640" cy="150" r="232" fill="#ffffff"/>
    </svg>

    <div class="brand">
      <span class="mark" aria-hidden="true"></span>
      <span class="name">Tidewell</span>
    </div>

    <ul class="contact-list">
      <li>
        <svg viewBox="0 0 24 24" aria-hidden="true"><path d="M6.6 10.8a15 15 0 0 0 6.6 6.6l2.2-2.2a1 1 0 0 1 1-.25 11.4 11.4 0 0 0 3.6.57 1 1 0 0 1 1 1V20a1 1 0 0 1-1 1A17 17 0 0 1 3 4a1 1 0 0 1 1-1h3.5a1 1 0 0 1 1 1c0 1.25.2 2.450.57 3.57a1 1 0 0 1-.25 1z"/></svg>
        84316570
      </li>
      <li>
        <svg viewBox="0 0 24 24" aria-hidden="true"><path d="M6 2h12v5H6zM4 8h16a2 2 0 0 1 2 2v7h-4v5H6v-5H2v-7a2 2 0 0 1 2-2zm4 8v4h8v-4z"/></svg>
        8431 6578
      </li>
      <li>
        <svg viewBox="0 0 24 24" aria-hidden="true"><path d="M2 5h20v14H2zm2 2v.5l8 5 8-5V7zm0 3v7h16v-7l-8 5z"/></svg>
        info@tidewellcareservices.com.au
      </li>
      <li>
        <svg viewBox="0 0 24 24" aria-hidden="true"><path d="M12 2a10 10 0 1 0 0 20 10 10 0 0 0 0-20zm-1 2.1V8H7.3A8 8 0 0 1 11 4.1zm2 0A8 8 0 0 1 16.7 8H13zM5.1 10H11v4H5.1a8 8 0 0 1 0-4zM13 10h5.9a8 8 0 0 1 0 4H13zM7.3 16H11v3.9A8 8 0 0 1 7.3 16zm5.7 0h3.7a8 8 0 0 1-3.7 3.9z"/></svg>
        www.tidewellcareservices.com.au
      </li>
      <li class="address">
        <svg viewBox="0 0 24 24" aria-hidden="true"><path d="M12 2a7 7 0 0 0-7 7c0 5 7 13 7 13s7-8 7-13a7 7 0 0 0-7-7zm0 9.5A2.5 2.5 0 1 1 12 6.5a2.5 2.5 0 0 1 0 5z"/></svg>
        14 Gallivant Ave Marlow Bay 3921
      </li>
    </ul>

    <p class="book-online">Book online</p>
    <p class="social">friendhub.net/TidewellOedemaAndFamilyCareClinic</p>
  </section>

</main>
</body>
</html>
```